VOMRA Pty Ltd Business Card

Looking for a simple yet eye-catching double-sided business card design using my company logo on one side and contact details on the other.

Target Market(s)

Government

Industry/Entity Type

Communication Systems Engineering

Contact Information for Business Card

VOMRA Pty Ltd

Requirements
Nice to have
• Would be great to have a QR code so details can be scanned into contacts

```html
<!DOCTYPE html>
<html lang="en">
<head>
<meta charset="utf-8">
<title>VOMRA Pty Ltd Business Card</title>
<link rel="stylesheet" href="https://fonts.googleapis.com/css2?family=Open+Sans:wght@400;700&display=swap">
<style>
  :root {
    --backdrop: #2a2d31;
    --card-white: #ffffff;
    --ink: #2e3a41;
    --ink-soft: #3d474d;
    --rule: #b9bdc0;
    --back-base: #3a444a;
    --back-pattern: #2c353b;
    --back-light: #5a6369;
  }
  * { box-sizing: border-box; margin: 0; padding: 0; }
  html, body {
    width: 1200px;
    height: 780px;
    overflow: hidden;
    background: var(--backdrop);
    font-family: "Open Sans", Arial, sans-serif;
  }
  .sheet {
    width: 1200px;
    height: 780px;
    display: flex;
    align-items: center;
    justify-content: center;
    gap: 48px;
  }
  .card {
    width: 540px;
    height: 309px;
    border-radius: 4px;
    box-shadow: 0 10px 30px rgba(0,0,0,.45);
    position: relative;
    overflow: hidden;
  }
  .card-front {
    background: var(--card-white);
    display: flex;
  }
  .brand-side {
    width: 46%;
    display: flex;
    align-items: center;
    justify-content: center;
    gap: 12px;
  }
  .brand-square {
    width: 22px;
    height: 22px;
    background: var(--ink);
  }
  .brand-name {
    font-weight: 700;
    font-size: 50px;
    letter-spacing: 2px;
    color: var(--ink);
  }
  .divider {
    position: absolute;
    left: 46%;
    top: 60px;
    bottom: 60px;
    width: 1px;
    background: linear-gradient(to bottom, transparent, var(--rule) 20%, var(--rule) 80%, transparent);
  }
  .details-side {
    width: 54%;
    padding: 0 22px 0 26px;
    display: flex;
    flex-direction: column;
    justify-content: center;
    color: var(--ink-soft);
  }
  .person-name {
    font-weight: 700;
    font-size: 25px;
    line-height: 1.1;
    color: var(--ink);
  }
  .person-role {
    font-size: 14px;
    margin-bottom: 8px;
  }
  .address {
    font-size: 15px;
    line-height: 1.3;
    margin-bottom: 6px;
  }
  .contact-list { list-style: none; }
  .contact-list li {
    display: flex;
    align-items: center;
    gap: 8px;
    font-size: 15px;
    line-height: 1.4;
  }
  .contact-list svg { width: 12px; height: 12px; flex: none; fill: var(--ink); }
  .card-back {
    background: linear-gradient(135deg, var(--back-pattern) 0%, var(--back-base) 60%, var(--back-light) 100%);
  }
</style>
</head>
<body>
  <main class="sheet">
    <section class="card card-front">
      <div class="brand-side">
        <span class="brand-square"></span>
        <span class="brand-name">VOMRA</span>
      </div>
      <div class="divider"></div>
      <div class="details-side">
        <h1 class="person-name">Jordan Pell</h1>
        <p class="person-role">Co-Founder</p>
        <p class="address">14-16 Harlow Lane Marrick<br>NSW 2099 Australia</p>
        <ul class="contact-list">
          <li>
            <svg viewBox="0 0 24 24" aria-hidden="true"><path d="M6.6 10.8a15.1 15.1 0 0 0 6.6 6.6l2.2-2.2a1 1 0 0 1 1-.25 11.4 11.4 0 0 0 3.6.57 1 1 0 0 1 1 1V20a1 1 0 0 1-1 1A17 17 0 0 1 3 4a1 1 0 0 1 1-1h3.5a1 1 0 0 1 1 1 11.4 11.4 0 0 0 .57 3.6 1 1 0 0 1-.25 1z"/></svg>
            (555) 014-2280
          </li>
          <li>
            <svg viewBox="0 0 24 24" aria-hidden="true"><circle cx="12" cy="12" r="10"/></svg>
            www.vomra.com.au
          </li>
          <li>
            <svg viewBox="0 0 24 24" aria-hidden="true"><path d="M2 5h20v14H2z M2 5l10 8 10-8" /></svg>
            admin@vomra.com.au
          </li>
        </ul>
      </div>
    </section>
    <section class="card card-back" role="img" aria-label="Dark slate back of card covered with a repeating pattern of the company mark"></section>
  </main>
</body>
</html>
```